Presentation Box for dry goods meat product

We would like a box designed for presentation on a shelf. Our product is fully cooked meats (beef, pork and chicken) that has a 12- to 18-month shelf-life without refrigeration. It's not dried food, but because of the cooking process it's succulent meat in sauce, storable at room temperature.Our anchor product will be "Timber Hollow Style Smoke Pot."The dimensions for the box will be approximately 8" tall by 5" wide and 2.5" deep.We have an oval-shaped (horizontal) logo in Navy, Crimson and Old Gold (think Dunmore Lanterns colors).
Updates

Reason: We haven't received enough options. We want the design to say "Timber Hollow Style Smoke Pot" not "Timber Hollow Style Smoke Pot." Use pictures of beef brisket (not steaks), pulled pork (not pork chops) and pulled chicken (not chicken legs/thighs).

Target Market(s)

Meat-buying consumers

Industry/Entity Type

Cooking

Requirements
Must have
• Space for ingredients and nutrition information. The name of our company is Merrow Foods.
Nice to have
• Picture of Bar-B-Que beef, pork and chicken

```html
<!DOCTYPE html>
<html lang="en">
<head>
<meta charset="utf-8">
<title>Timber Hollow Style Smoke Pot – Box Panels</title>
<link rel="stylesheet" href="https://fonts.googleapis.com/css2?family=Oswald:wght@500;700&family=Roboto+Condensed:wght@400;700&display=swap">
<style>
  :root {
    --stage: #eceef1;
    --navy: #1c2458;
    --navy-deep: #10163a;
    --crimson: #b3141c;
    --crimson-deep: #6e0b10;
    --gold: #d9b25c;
    --gold-deep: #9a7526;
    --white: #ffffff;
    --ink: #1a1a1a;
    --meat-light: #b8673a;
    --meat-dark: #4a1f10;
  }
  * { margin: 0; padding: 0; box-sizing: border-box; }
  html, body { width: 1200px; height: 943px; overflow: hidden; }
  body {
    background: var(--stage);
    font-family: "Roboto Condensed", "Arial Narrow", sans-serif;
  }
  .dieline {
    position: absolute;
    left: 300px; top: 150px;
    width: 600px; height: 640px;
    display: flex;
    box-shadow: 0 18px 40px rgba(0,0,0,.18);
  }

  /* Front panel */
  .front-panel {
    position: relative;
    width: 400px; height: 640px;
    background: linear-gradient(160deg, var(--navy) 0%, var(--navy-deep) 100%);
    overflow: hidden;
  }
  .brand-strip {
    position: absolute;
    left: 16px; top: 0;
    width: 70px; height: 300px;
    background: var(--white);
  }
  .brand-name {
    display: flex; align-items: center; gap: 4px;
    padding: 28px 4px 0 6px;
    color: var(--navy);
    font-weight: 700;
    font-size: 11px;
    line-height: 1.05;
  }
  .brand-dot {
    flex: none;
    width: 8px; height: 8px; border-radius: 50%;
    background: var(--crimson);
  }
  .product-title {
    position: absolute;
    left: 100px; top: 100px;
    width: 292px;
    color: var(--gold);
    font-family: "Oswald", sans-serif;
    font-weight: 700;
    font-size: 35px;
    line-height: 1.25;
    white-space: nowrap;
    text-align: center;
    text-shadow: 0 2px 3px rgba(0,0,0,.45);
  }
  .panel-art { position: absolute; left: 0; top: 0; }
  .net-weight {
    position: absolute;
    left: 14px; bottom: 14px;
    color: var(--white);
    font-weight: 700;
    font-size: 12px;
    letter-spacing: .5px;
  }

  /* Side panel */
  .side-panel {
    position: relative;
    width: 200px; height: 640px;
    background: linear-gradient(180deg, var(--navy) 0%, var(--navy-deep) 100%);
    color: var(--white);
  }
  .nutrition-facts {
    position: absolute;
    left: 12px; top: 16px;
    width: 176px;
    background: var(--white);
    color: var(--ink);
    padding: 6px 8px;
    font-size: 9px;
    line-height: 1.35;
  }
  .nutrition-facts h2 {
    font-family: "Oswald", sans-serif;
    font-weight: 700;
    font-size: 19px;
    line-height: 1.05;
    border-bottom: 1px solid var(--ink);
    padding-bottom: 2px;
  }
  .nf-row { display: flex; justify-content: space-between; border-bottom: 1px solid #999; }
  .nf-row.thick { border-bottom: 4px solid var(--ink); }
  .nf-row.sub { padding-left: 8px; }
  .nf-bold { font-weight: 700; }
  .nf-note { font-size: 7.5px; padding-top: 3px; }
  .diet-claims {
    position: absolute;
    left: 0; top: 330px; width: 200px;
    text-align: center;
    font-weight: 700;
    font-size: 13px;
    line-height: 1.35;
  }
  .ingredients {
    position: absolute;
    left: 16px; top: 390px; width: 168px;
    font-size: 9px; line-height: 1.45;
    text-transform: uppercase;
  }
  .packer {
    position: absolute;
    left: 16px; top: 470px; width: 168px;
    font-size: 9px; line-height: 1.45;
  }
</style>
</head>
<body>
  <main class="dieline">
    <section class="front-panel">
      <svg class="panel-art" width="400" height="640" viewBox="0 0 400 640">
        <defs>
          <linearGradient id="bandFill" x1="0" y1="0" x2="0" y2="1">
            <stop offset="0" stop-color="#b3141c"/>
            <stop offset="1" stop-color="#6e0b10"/>
          </linearGradient>
          <linearGradient id="meatFill" x1="0" y1="0" x2="1" y2="1">
            <stop offset="0" stop-color="#b8673a"/>
            <stop offset=".6" stop-color="#7a3419"/>
            <stop offset="1" stop-color="#4a1f10"/>
          </linearGradient>
          <linearGradient id="sealRing" x1="0" y1="0" x2="1" y2="1">
            <stop offset="0" stop-color="#d9b25c"/>
            <stop offset="1" stop-color="#9a7526"/>
          </linearGradient>
        </defs>
        <path class="title-swoosh" d="M150 232 Q250 222 340 214" stroke="#b3141c" stroke-width="5" stroke-linecap="round" fill="none"/>
        <path class="crimson-band" d="M0 330 Q180 290 400 300 L400 420 Q200 400 0 440 Z" fill="url(#bandFill)"/>
        <path class="meat-photo" role="img" aria-label="Photo of barbecued meat with a lettuce garnish" d="M0 380 Q120 330 260 360 Q340 380 400 420 L400 640 L0 640 Z" fill="url(#meatFill)"/>
        <g class="quality-seal">
          <circle cx="322" cy="320" r="40" fill="url(#sealRing)"/>
          <circle cx="322" cy="320" r="31" fill="#10163a"/>
        </g>
      </svg>

      <div class="brand-strip">
        <div class="brand-name"><span class="brand-dot"></span><span>Merrow Foods</span></div>
      </div>
      <h1 class="product-title">Timber Hollow Style<br>Smoke Pot</h1>
      <p class="net-weight">NET WT 5 oz</p>
    </section>

    <section class="side-panel">
      <div class="nutrition-facts">
        <h2>Nutrition Facts</h2>
        <div class="nf-row"><span>Serving Size 1/2 cup (70g)</span></div>
        <div class="nf-row thick"><span>Servings Per Box 2</span></div>
        <div class="nf-row nf-bold"><span>Amount Per Serving</span></div>
        <div class="nf-row thick nf-bold"><span>Calories 180</span></div>
        <div class="nf-row"><span></span><span class="nf-bold">% Daily Value</span></div>
        <div class="nf-row"><span class="nf-bold">Total Fat 6g</span><span>9%</span></div>
        <div class="nf-row"><span class="nf-bold">Sodium 420mg</span><span>18%</span></div>
        <div class="nf-row"><span class="nf-bold">Total Carbohydrate 12g</span><span>4%</span></div>
        <div class="nf-row sub"><span>Sugars 9g</span></div>
        <div class="nf-row thick"><span class="nf-bold">Protein 18g</span></div>
        <div class="nf-row"><span>Vitamin A 2% • Iron 8%</span></div>
        <p class="nf-note">Percent Daily Values are based on a 2,000 calorie diet.</p>
      </div>

      <p class="diet-claims">GLUTEN FREE<br>MALTITOL FREE</p>
      <p class="ingredients">Ingredients: beef, pork, chicken, tomato, vinegar, brown sugar, spices, salt.</p>
      <p class="packer">Packed for Merrow Foods, 214 Alder Lane, Brookfield</p>
    </section>
  </main>
</body>
</html>
```